Business card for Sports Apparel business

DOUBLE SIDED DESIGN
We need business cards for a new sports apparel business. We are developing a protective headband for soccer initially.
Torvalle is focused on designing and developing head protection products to reduce the likelihood of concussion when playing sports. Exploring and understanding medical insights, material science research, current and former players experiences and governing bodies guidelines has allowed Torvalle to develop the safety, style, form and function requirements of a suitable product to bring to market.
Target Market(s)
Mums buying kits for the sons and daughters. Amateur footballers.
Industry/Entity Type
Sporting Good
Contact Information for Business Card
Martin Ashworth - CEO
Mobile: +44 7431589027
Email: martin@torvalle.co.uk
Tel: 0208 5519372
Helena Pargeter - COO
Mob: +44 7385 640117
Email: helena@torvalle.co.uk
Tel: 0208 5519372
Duncan Farrow - CCO
Mob: +44 7564 293081
Email: duncan@torvalle.co.uk
Tel: 0208 5519372
Look and feel
Each slider illustrates characteristics of the customer's brand and the style your logo design should communicate.

```html
<!DOCTYPE html>
<html lang="en">
<head>
<meta charset="utf-8">
<title>Torvalle Business Card</title>
<link rel="stylesheet" href="https://fonts.googleapis.com/css2?family=Montserrat:wght@300;400;600&family=Oswald:wght@500&display=swap">
<style>
  :root {
    --brand-blue: #0a5b96;
    --brand-grey: #5f5f61;
    --rule-grey: #707072;
    --card-white: #ffffff;
    --page-bg: #e6e7e9;
  }
  * { box-sizing: border-box; margin: 0; padding: 0; }
  html, body { width: 1200px; height: 900px; overflow: hidden; }
  body {
    background: var(--page-bg);
    position: relative;
    font-family: "Montserrat", sans-serif;
  }
  .card {
    position: absolute;
    left: 250px;
    width: 700px;
    height: 400px;
    border-radius: 22px;
    overflow: hidden;
  }
  .card--back { top: 30px; background: var(--brand-blue); }
  .card--front { top: 470px; background: var(--card-white); }

  .wordmark {
    position: absolute;
    left: 0; right: 0;
    text-align: center;
    font-family: "Montserrat", sans-serif;
    font-weight: 600;
    letter-spacing: 4px;
  }
  .card--back .wordmark { top: 158px; font-size: 68px; color: var(--card-white); }
  .card--front .wordmark { top: 80px; font-size: 76px; color: var(--brand-grey); }

  .front-rule {
    position: absolute;
    left: 0; right: 0; top: 250px;
    height: 6px;
    background: var(--rule-grey);
  }
  .front-band {
    position: absolute;
    left: 0; right: 0; top: 256px; bottom: 0;
    background: var(--brand-blue);
    color: var(--card-white);
  }
  .person {
    position: absolute;
    right: 400px; top: 40px;
    text-align: right;
  }
  .person__name {
    font-family: "Oswald", sans-serif;
    font-weight: 500;
    font-size: 27px;
    letter-spacing: 2px;
    text-transform: uppercase;
    line-height: 1.1;
  }
  .person__role {
    font-weight: 300;
    font-size: 20px;
    letter-spacing: 1px;
    margin-top: 4px;
  }
  .band-divider {
    position: absolute;
    left: 320px; top: 24px;
    width: 2px; height: 100px;
    background: var(--card-white);
  }
  .contacts {
    position: absolute;
    left: 350px; top: 26px;
    list-style: none;
  }
  .contacts li {
    display: flex;
    align-items: center;
    gap: 12px;
    font-size: 18px;
    font-weight: 400;
    letter-spacing: 0.5px;
    line-height: 24px;
  }
  .contacts svg { width: 16px; height: 16px; flex: none; }
</style>
</head>
<body>
  <section class="card card--back" aria-label="Card back">
    <div class="wordmark">TORVALLE</div>
  </section>

  <section class="card card--front" aria-label="Card front">
    <div class="wordmark">TORVALLE</div>
    <div class="front-rule"></div>
    <div class="front-band">
      <div class="person">
        <div class="person__name">Helena Pargeter</div>
        <div class="person__role">COO</div>
      </div>
      <div class="band-divider"></div>
      <ul class="contacts">
        <li>
          <svg viewBox="0 0 16 16" aria-hidden="true"><path d="M4 1.5l2.2 2.6-1.3 1.6c.8 2 2.4 3.7 4.4 4.6l1.6-1.3 2.6 2.2-1.4 2.3C7.5 13.6 2.4 8.5 1.7 3.2z" fill="#fff"/></svg>
          <span>0208 5519372</span>
        </li>
        <li>
          <svg viewBox="0 0 16 16" aria-hidden="true"><rect x="4" y="1" width="8" height="14" rx="1.5" fill="none" stroke="#fff" stroke-width="1.5"/><circle cx="8" cy="12.3" r="0.9" fill="#fff"/></svg>
          <span>+44 7385 640117</span>
        </li>
        <li>
          <svg viewBox="0 0 16 16" aria-hidden="true"><rect x="1.5" y="3.5" width="13" height="9" fill="none" stroke="#fff" stroke-width="1.4"/><path d="M1.5 3.5L8 9l6.5-5.5" fill="none" stroke="#fff" stroke-width="1.4"/></svg>
          <span>helena@torvalle.co.uk</span>
        </li>
        <li>
          <svg viewBox="0 0 16 16" aria-hidden="true"><g fill="none" stroke="#fff" stroke-width="1.2"><circle cx="8" cy="8" r="6.5"/><ellipse cx="8" cy="8" rx="3" ry="6.5"/><path d="M1.5 8h13M2.5 4.8h11M2.5 11.2h11"/></g></svg>
          <span>www.torvalle.co.uk</span>
        </li>
      </ul>
    </div>
  </section>
</body>
</html>
```